Powerpoint, Graphics for Sermon Series

I am starting a sermon series on the short letters if Scripture that are between Hebrews and Revelation. The sermon series will be called "Walking Unmarked Trails: Lasting Lessons from Quiet Hills."

Think about finding a packet of letters in an Attic. There is only the dialogue of the writer. We don't know exactly what the receivers were going through or even what their response to the letters were/are!

Target Market(s)

Local Church

Industry/Entity Type

Christian

Font styles to use
Serif
Sans Serif

Colors

Designer to choose colors to be used in the design.

Requirements
Must have
• Powerpoint Slide with Title -
• Background Slide -
• It would be great to have both JPG, PNG, and Photoshop/Indesign that can be used for powerpoint, both in 4x3 ration and wide... Need Title Slide with typography and background slide for text to go over the top of.
• Stick with the theme -- Walking Unmarked Trails
• I am including our church logo, but don't feel like you need to use it in anyway.
Nice to have
• Social Media Slides - Square Slide, Facebook Header
• Greyscale Version?

```html
<!DOCTYPE html>
<html lang="en">
<head>
<meta charset="utf-8">
<title>Walking Unmarked Trails – Text Slide</title>
<link rel="stylesheet" href="https://fonts.googleapis.com/css2?family=Lato:wght@400;700&display=swap">
<style>
  :root {
    --paper-light: #d8c0a6;
    --paper-mid: #a9845f;
    --paper-dark: #5e3f28;
    --panel: rgba(248, 240, 236, 0.93);
    --title: #b3461a;
    --body: #3a2a22;
    --brand: #4a2f1f;
  }
  * { margin: 0; padding: 0; box-sizing: border-box; }
  html, body { width: 1200px; height: 900px; overflow: hidden; }
  body { font-family: "Lato", sans-serif; background: var(--paper-mid); }

  .slide {
    position: relative;
    width: 1200px;
    height: 900px;
    overflow: hidden;
  }

  .slide__backdrop {
    position: absolute;
    inset: 0;
    background:
      radial-gradient(ellipse at 38% 30%, rgba(240, 222, 200, 0.55), transparent 55%),
      linear-gradient(125deg, var(--paper-light) 0%, var(--paper-mid) 45%, var(--paper-dark) 100%);
  }

  .brand {
    position: absolute;
    top: 42px;
    right: 36px;
    display: flex;
    align-items: center;
    gap: 12px;
    font-weight: 700;
    font-size: 34px;
    color: var(--brand);
    letter-spacing: 0.5px;
  }
  .brand__mark {
    width: 18px;
    height: 18px;
    border-radius: 50%;
    background: var(--brand);
  }

  .text-panel {
    position: absolute;
    left: 0;
    top: 115px;
    width: 603px;
    height: 650px;
    background: var(--panel);
    border-radius: 0 22px 22px 0;
    padding: 34px 30px 0 48px;
  }
  .text-panel__title {
    font-weight: 700;
    font-size: 36px;
    line-height: 1.2;
    color: var(--title);
    margin-bottom: 4px;
  }
  .text-panel__body {
    font-size: 22px;
    line-height: 37.5px;
    color: var(--body);
  }
</style>
</head>
<body>
  <main class="slide">
    <div class="slide__backdrop" role="img" aria-label="Photograph of an old open book with worn printed pages in warm sepia tones"></div>

    <div class="brand">
      <span class="brand__mark"></span>
      <span class="brand__name">Cedar Path Church</span>
    </div>

    <section class="text-panel">
      <h2 class="text-panel__title">Subtext title here</h2>
      <p class="text-panel__body">Lorem Ipsum is simply dummy text of the printing and typesetting industry. Lorem Ipsum has been the industry's standard dummy text ever since the 1500s, when an unknown printer took a galley of type and scrambled it to make a type specimen book. It has survived not only five centuries, but also the leap into electronic typesetting, remaining essentially unchanged. It was popularised in the 1960s with the release of Letraset sheets containing Lorem Ipsum passages, and more recently with desktop Lorem Ipsum has been the industry's standard dummy text ever since the 1500s, when an unknown printer took a galley of type and scrambled it to make a type specimen book. It has survived not only five</p>
    </section>
  </main>
</body>
</html>
```